Software allocation system needs a business card design

We need a business card designed for our software platform - www.tallivo.com.au

At the moment the logo and website is all black and white, we are happy for suggestions on implementing some colour throughout either the logo or business card.

Industry/Entity Type

Software

Font styles to use
Sans Serif

Colors

Designer to choose colors to be used in the design.

```html
<!DOCTYPE html>
<html lang="en">
<head>
<meta charset="utf-8">
<title>Tallivo Business Card</title>
<link rel="stylesheet" href="https://fonts.googleapis.com/css2?family=Jost:wght@300;400;500&display=swap">
<style>
  :root {
    --backdrop: #e9ecee;
    --card: #ffffff;
    --band-blue: #1e88b8;
    --mark-blue: #3a9bc4;
    --heading-blue: #1d6f99;
    --text-blue: #3d9cc6;
    --tagline-teal: #7cc3c0;
    --name-grey: #4a4f57;
  }
  * { margin: 0; padding: 0; box-sizing: border-box; }
  html, body {
    width: 1200px;
    height: 900px;
    overflow: hidden;
    background: var(--backdrop);
    font-family: "Jost", sans-serif;
  }
  .business-card {
    position: absolute;
    left: 100px;
    top: 145px;
    width: 1000px;
    height: 611px;
    background: var(--card);
    overflow: hidden;
    box-shadow: 0 10px 30px rgba(0, 0, 0, 0.12);
  }
  .accent-band {
    position: absolute;
    inset: 0;
    width: 1000px;
    height: 611px;
  }
  .brand {
    position: absolute;
    left: 120px;
    top: 175px;
  }
  .brand-name {
    display: flex;
    align-items: center;
    gap: 14px;
    font-size: 66px;
    font-weight: 300;
    letter-spacing: 6px;
    color: var(--name-grey);
    line-height: 1;
  }
  .brand-dot {
    width: 40px;
    height: 40px;
    border-radius: 50%;
    background: var(--mark-blue);
  }
  .brand-tagline {
    margin-top: 12px;
    font-size: 17px;
    font-weight: 400;
    letter-spacing: 2px;
    text-transform: uppercase;
    color: var(--tagline-teal);
  }
  .corner-mark {
    position: absolute;
    right: 80px;
    top: 55px;
    display: flex;
    align-items: center;
    gap: 16px;
  }
  .corner-mark-circle {
    width: 70px;
    height: 70px;
    border-radius: 50%;
    background: var(--mark-blue);
  }
  .corner-mark-name {
    font-size: 34px;
    font-weight: 400;
    letter-spacing: 3px;
    color: var(--mark-blue);
    white-space: nowrap;
  }
  .contact {
    position: absolute;
    left: 440px;
    top: 460px;
    color: var(--text-blue);
  }
  .contact-heading {
    font-size: 34px;
    font-weight: 500;
    color: var(--heading-blue);
    margin-bottom: 8px;
  }
  .contact-line {
    font-size: 22px;
    font-weight: 300;
    line-height: 1.3;
  }
</style>
</head>
<body>
  <main class="business-card">
    <svg class="accent-band" viewBox="0 0 1000 611" aria-hidden="true">
      <polygon points="0,470 1000,150 1000,230 380,430 260,611 0,611" fill="var(--band-blue)"/>
    </svg>

    <div class="corner-mark">
      <span class="corner-mark-circle"></span>
      <span class="corner-mark-name">TALLIVO</span>
    </div>

    <header class="brand">
      <div class="brand-name"><span class="brand-dot"></span>TALLIVO</div>
      <p class="brand-tagline">Planning &amp; compliance for heavy industry</p>
    </header>

    <section class="contact">
      <h2 class="contact-heading">Contac Us</h2>
      <p class="contact-line">PO Box 512</p>
      <p class="contact-line">Harbourvale NSW 2071</p>
      <p class="contact-line">hello@tallivo.com.au</p>
    </section>
  </main>
</body>
</html>
```